Digital Marketing Agency Landing Page

At VELIM, we offer a comprehensive solution for solar companies' client acquisition needs in the rapidly growing industry. We handle end-to-end client acquisition, meaning we manage the entire lifecycle of capturing new clients—from initial lead generation to delivering the ready-to-buy homeowner. Our expertise in targeted advertising, data analytics, and customer relationship management ensures that we not only find potential customers but also nurture them through tailored engagement strategies until they are ready to make a purchase. By entrusting us with your client acquisition process, solar companies can focus on what they do best—providing sustainable energy solutions—while we work behind the scenes to grow your customer base and increase your market share.

We need to restructure our website to make it more professional. We don't need any complex functionalities. We are looking for someone that is good in design and can build a visually aesthetic website following our brand image. We only need a landing page and a lead form in the end. I would like to have only one page, but a relatively big one where people scroll down. I would like to have a minimal and classy look. Something that is timeless and elegant.

Structure:

initial page
About us
How we operate
Get in touch

Target Market(s)

Solar Comapanies

Industry/Entity Type

Marketing solautions

Coding

Coded - Design and coding required

Number of Pages Required

1 page

Requirements
Nice to have
• Inspirations: https://www.qz.zu/ https://www.marchbeck.example/ https://www.tovanrid.example/ https://pruvo.example/

```html
<!DOCTYPE html>
<html lang="en">
<head>
<meta charset="utf-8">
<title>VELIM — Client Acquisition for Solar Companies</title>
<link href="https://fonts.googleapis.com/css2?family=Montserrat:wght@400;500;600;700&display=swap" rel="stylesheet">
<style>
:root{
  --navy:#13212e;
  --navy-soft:#1e2d3b;
  --cream:#ebe6d8;
  --sand:#f6f3ec;
  --white:#ffffff;
  --text:#6f6f6f;
  --rule:#a5a5a5;
}
*{margin:0;padding:0;box-sizing:border-box}
html,body{width:1200px;height:2415px;overflow:hidden}
body{font-family:'Montserrat',sans-serif;color:var(--navy);background:var(--white);position:relative}
.abs{position:absolute}

/* header */
.site-header{position:absolute;left:0;top:0;width:1200px;height:123px;background:var(--navy)}
.brand{position:absolute;height:81px;color:var(--white);font-size:44px;font-weight:500;letter-spacing:1px;display:flex;align-items:center;gap:14px}
.brand-mark{width:14px;height:14px;background:var(--cream);display:block}
.main-nav{position:absolute;left:522px;top:52px;display:flex;gap:30px}
.main-nav a{color:var(--white);text-decoration:none;font-size:16px;font-weight:500;padding-bottom:5px}
.main-nav a.active{border-bottom:2px solid var(--white)}
.socials{position:absolute;display:flex;gap:4px}
.socials span{width:38px;height:38px;border-radius:50%;border:1.5px solid var(--white);display:block}

/* hero */
.hero{position:absolute;left:0;top:123px;width:1200px;height:618px;
  background:linear-gradient(160deg,#6f8aa3 0%,#a9a686 30%,#d9b25a 60%,#8a8b3a 80%,#4e5a2a 100%)}
.hero-shade{position:absolute;left:0;top:0;width:1200px;height:618px;background:linear-gradient(90deg,rgba(20,30,60,.45) 0%,rgba(40,50,90,.2) 45%,rgba(40,50,90,0) 70%)}
.hero-title{position:absolute;left:112px;top:200px;color:var(--white);font-size:47px;font-weight:600}
.hero-lead{position:absolute;left:112px;top:270px;width:400px;color:var(--white);font-size:21px;line-height:31px}
.btn-outline{position:absolute;left:112px;top:357px;width:131px;height:46px;border:1.5px solid var(--white);color:var(--white);font-size:13px;font-weight:500;display:flex;align-items:center;justify-content:center}
.btn-outline::after{content:"";position:absolute;left:7px;top:7px;width:131px;height:46px;border:1.5px solid var(--white)}

.contact-card{position:absolute;left:738px;top:222px;width:350px;height:418px;background:rgba(235,230,216,.55)}
.contact-inner{position:absolute;left:8px;top:9px;width:333px;height:402px;background:var(--cream)}
.contact-inner h2{position:absolute;left:0;width:333px;top:40px;text-align:center;font-size:24px;font-weight:700}
.contact-inner .rule{position:absolute;left:136px;top:73px;width:62px;height:3px;background:var(--rule)}
.field{position:absolute;left:34px;width:265px;height:41px;background:var(--white);display:flex;align-items:center;padding-left:15px;gap:9px;font-family:Arial,sans-serif;font-size:13px;color:#333;box-shadow:0 2px 4px rgba(0,0,0,.06)}
.field svg{width:12px;height:12px;fill:#555}
.submit{position:absolute;left:34px;top:317px;width:265px;height:41px;background:var(--navy);color:var(--white);font-size:15px;font-weight:600;display:flex;align-items:center;justify-content:center}

/* about */
.photo{position:absolute}
.about-title{position:absolute;left:675px;top:896px;font-size:41px;font-weight:700}
.about-rule{position:absolute;left:675px;top:945px;width:75px;height:3px;background:var(--rule)}
.about-text{position:absolute;left:675px;width:413px;font-size:16px;line-height:26.7px;color:var(--text);text-align:justify}
.btn-learn{position:absolute;left:675px;top:1243px;width:143px;height:48px;background:var(--cream);font-size:15px;font-weight:600;display:flex;align-items:center;justify-content:center}
.btn-learn-frame{position:absolute;left:684px;top:1252px;width:143px;height:48px;border:2px solid var(--navy);border-top:none}

/* services */
.services{position:absolute;left:0;top:1462px;width:1200px;height:607px;background:var(--sand)}
.section-title{position:absolute;left:0;width:1200px;text-align:center;font-size:41px;font-weight:700}
.service-card{position:absolute;top:169px;width:305px;height:356px;background:var(--white);text-align:center;box-shadow:0 4px 14px rgba(0,0,0,.05)}
.service-card.dark{background:var(--navy);color:var(--white)}
.service-card svg.diamond{position:absolute;left:100px;top:36px}
.service-card h3{position:absolute;left:0;width:305px;top:160px;font-size:18px;font-weight:700;line-height:25px}
.service-card p{position:absolute;left:20px;width:265px;top:219px;font-size:16px;line-height:26.5px;color:var(--text)}
.service-card.dark p{color:var(--white)}

/* footer */
.site-footer{position:absolute;left:0;top:2069px;width:1200px;height:294px;background:var(--navy);color:var(--white)}
.footer-heading{position:absolute;top:54px;font-size:17px;font-weight:600}
.quick-links a{position:absolute;color:var(--white);text-decoration:none;font-size:15px}
.chev{position:absolute;left:384px;font-size:13px}
.info-label{position:absolute;left:600px;font-size:15px;font-weight:600}
.info-value{position:absolute;left:600px;font-size:12.5px;line-height:19px}
.info-icon{position:absolute;left:566px;width:14px;height:14px;fill:var(--rule)}
.newsletter{position:absolute;left:805px;top:102px;width:283px;height:48px;background:var(--sand);border:3px solid var(--white)}
.newsletter .placeholder{position:absolute;left:15px;top:13px;font-size:15px;color:#555}
.newsletter .signup{position:absolute;right:0;top:0;width:103px;height:42px;background:var(--navy);font-size:15px;font-weight:700;display:flex;align-items:center;justify-content:center;color:var(--white)}
.footer-socials span{width:36px;height:36px;border-radius:50%;border:1.5px solid var(--white);display:block}
.footer-socials span.filled{background:var(--sand)}
.copyright{position:absolute;left:0;top:2363px;width:1200px;height:52px;background:var(--navy-soft);color:var(--white);font-size:13.5px;display:flex;align-items:center;justify-content:center;gap:6px}
</style>
</head>
<body>

<header class="site-header">
  <div class="brand" style="left:112px;top:21px"><span class="brand-mark"></span>VELIM</div>
  <nav class="main-nav">
    <a class="active">HOME</a><a>ABOUT US</a><a>SERVICES</a><a>CONTACT US</a>
  </nav>
  <div class="socials" style="left:968px;top:43px" aria-label="Social links"><span></span><span></span><span></span></div>
</header>

<section class="hero">
  <div role="img" aria-label="Rows of solar panels in a grassy field at sunrise, trees in golden light" style="position:absolute;inset:0"></div>
  <div class="hero-shade"></div>
  <h1 class="hero-title">VELIM</h1>
  <p class="hero-lead">Lorem ipsum dolor sit amet, consec tetu adipiscing elit sedea.</p>
  <div class="btn-outline">GET STARTED</div>

  <div class="contact-card">
    <div class="contact-inner">
      <h2>CONTACT US</h2>
      <div class="rule"></div>
      <div class="field" style="top:104px"><svg viewBox="0 0 12 12"><circle cx="6" cy="3.5" r="2.8"/><path d="M1 12c0-3.5 2.2-5 5-5s5 1.5 5 5z"/></svg>Your Name</div>
      <div class="field" style="top:154px"><svg viewBox="0 0 12 12"><path d="M2.5 0.5l2 2.5-1.2 1.5c.8 1.8 2.4 3.4 4.2 4.2l1.5-1.2 2.5 2-1.5 2C5 11 1 7 .5 2z"/></svg>Phone</div>
      <div class="field" style="top:206px"><svg viewBox="0 0 12 12"><path d="M0 2h12v1L6 7 0 3zM0 4.5l6 4 6-4V10H0z"/></svg>Email</div>
      <div class="field" style="top:257px"><svg viewBox="0 0 12 12"><path d="M2 0h8v12H7V9.5H5V12H2zM3.5 2v1.5h1.5V2zm3.5 0v1.5h1.5V2zM3.5 5v1.5h1.5V5zm3.5 0v1.5h1.5V5z"/></svg>Company</div>
      <div class="submit">SUBMIT</div>
    </div>
  </div>
</section>

<section class="about">
  <div class="photo" role="img" aria-label="Colleagues at a desk with a laptop reviewing documents" style="left:112px;top:866px;width:343px;height:386px;background:linear-gradient(150deg,#e4e8ea,#c9c2b8 55%,#3b3028)"></div>
  <div class="photo" style="left:310px;top:1030px;width:282px;height:300px;background:var(--white)"></div>
  <div class="photo" role="img" aria-label="Hands pointing at charts on a tablet during a meeting" style="left:319px;top:1039px;width:273px;height:291px;background:linear-gradient(160deg,#d8c7a8,#a88a64 50%,#5b4a3b)"></div>
  <div class="photo" role="img" aria-label="Decorative grid of dots" style="left:174px;top:1261px;width:129px;height:39px;background:#f1f1f1"></div>

  <h2 class="about-title">ABOUT US</h2>
  <div class="about-rule"></div>
  <p class="about-text" style="top:979px">Lorem ipsum dolor sit amet, consectetur adipiscing elit, sed do eiusmod tempor incididunt ut labore et dolore magna aliqua ut enim ad minim veniam, quis nostrud exercitation ullamco laboris nisi ut aliquip ex ealiqua ut enim ad minim veniama.</p>
  <p class="about-text" style="top:1126px">Lorem ipsum dolor sit amet, consectetur adipiscing elit, sed do eiusmod tempor incididunt ut labore et dolore magna aliqua.</p>
  <div class="btn-learn-frame"></div>
  <div class="btn-learn">LEARN MORE</div>
</section>

<section class="services">
  <h2 class="section-title" style="top:71px">OUR SERVICES</h2>
  <div class="abs" style="left:562px;top:122px;width:75px;height:3px;background:var(--rule)"></div>

  <article class="service-card" style="left:112px">
    <svg class="diamond" width="105" height="105" viewBox="0 0 105 105"><path d="M52.5 0L105 52.5 52.5 105 0 52.5z" fill="#13212e"/><g fill="none" stroke="#fff" stroke-width="1.6"><rect x="36" y="44" width="22" height="16"/><path d="M60 50l10-6v20l-10-6z"/><circle cx="66" cy="38" r="4"/></g></svg>
    <h3>ADVERTISING</h3>
    <p>Lorem ipsum dolor sit amet, con sectetur adipiscing elit, sed do eiusmod tempor incididunt ut labore et dolorea.</p>
  </article>

  <article class="service-card dark" style="left:447px">
    <svg class="diamond" width="105" height="105" viewBox="0 0 105 105"><path d="M52.5 0L105 52.5 52.5 105 0 52.5z" fill="#ebe6d8"/><g fill="none" stroke="#13212e" stroke-width="1.6"><rect x="34" y="36" width="34" height="26"/><path d="M40 56v-6M46 56v-10M52 56v-8M58 56v-12"/><circle cx="62" cy="60" r="6"/><path d="M66 64l6 6"/></g></svg>
    <h3>DATA<br>ANALYTICS</h3>
    <p>Lorem ipsum dolor sit amet, con sectetur adipiscing elit, sed do eiusmod tempor incididunt ut labore et dolorea.</p>
  </article>

  <article class="service-card" style="left:784px">
    <svg class="diamond" width="105" height="105" viewBox="0 0 105 105"><path d="M52.5 0L105 52.5 52.5 105 0 52.5z" fill="#13212e"/><g fill="none" stroke="#fff" stroke-width="1.6"><circle cx="44" cy="42" r="5"/><circle cx="61" cy="42" r="5"/><path d="M34 60c0-7 4-10 10-10s10 3 10 10M51 60c0-7 4-10 10-10s10 3 10 10"/></g></svg>
    <h3>CUSTOMER<br>RELATIONSHIP</h3>
    <p>Lorem ipsum dolor sit amet, con sectetur adipiscing elit, sed do eiusmod tempor incididunt ut labore et dolorea.</p>
  </article>
</section>

<footer class="site-footer">
  <div class="brand" style="left:112px;top:120px"><span class="brand-mark"></span>VELIM</div>

  <h4 class="footer-heading" style="left:384px">QUICK LINKS</h4>
  <div class="quick-links">
    <span class="chev" style="top:100px">»</span><a style="left:417px;top:98px">Home</a>
    <span class="chev" style="top:147px">»</span><a style="left:417px;top:145px">About Us</a>
    <span class="chev" style="top:193px">»</span><a style="left:417px;top:191px">Services</a>
    <span class="chev" style="top:239px">»</span><a style="left:417px;top:237px">Contact Us</a>
  </div>

  <h4 class="footer-heading" style="left:566px">CONTACT INFO</h4>
  <svg class="info-icon" style="top:101px" viewBox="0 0 14 14"><path d="M7 0a4.5 4.5 0 0 0-4.5 4.5C2.5 8 7 14 7 14s4.5-6 4.5-9.5A4.5 4.5 0 0 0 7 0zm0 6.3a1.8 1.8 0 1 1 0-3.6 1.8 1.8 0 0 1 0 3.6z"/></svg>
  <div class="info-label" style="top:98px">LOCATION:</div>
  <div class="info-value" style="top:122px">72 Harlow Lane, Brookfield,<br>CO, United States</div>
  <svg class="info-icon" style="top:171px" viewBox="0 0 12 12"><path d="M2.5 0.5l2 2.5-1.2 1.5c.8 1.8 2.4 3.4 4.2 4.2l1.5-1.2 2.5 2-1.5 2C5 11 1 7 .5 2z"/></svg>
  <div class="info-label" style="top:169px">PHONE:</div>
  <div class="info-value" style="top:192px">+1 (555) 014 2290</div>
  <svg class="info-icon" style="top:224px" viewBox="0 0 12 12"><path d="M0 2h12v1L6 7 0 3zM0 4.5l6 4 6-4V10H0z"/></svg>
  <div class="info-label" style="top:222px">EMAIL:</div>
  <div class="info-value" style="top:243px">info@velim.example</div>

  <h4 class="footer-heading" style="left:805px">NEWSLETTER SIGNUP</h4>
  <div class="newsletter"><span class="placeholder">Email Address</span><span class="signup">SIGN UP</span></div>
  <div class="socials footer-socials" style="left:805px;top:175px;gap:6px" aria-label="Social links"><span class="filled"></span><span></span><span></span></div>
</footer>

<div class="copyright">© 2023 <strong style="font-weight:600">VELIM</strong> | &nbsp;All Rights Reserved</div>

</body>
</html>
```